Demolition Company Billboard Design 13 feet wide 15 feet high

This is my first billboard on a busy road. I want it to be professional but with some eye catching flair that matches by business which is a demoltion business and also list my services. My company slogan is also

"watch kessel clear the lot"

Target Market(s)

Home Ownerd and General Construction Companies

Industry/Entity Type

construction

Colors
0054AA
0677BA
7BADD7
CADEEF
E8F1F8

Requirements
Must have
• My services listed in the pictures my website and my phone number

```html
<!DOCTYPE html>
<html lang="en">
<head>
<meta charset="utf-8">
<title>Kessel Demolition Billboard</title>
<link href="https://fonts.googleapis.com/css2?family=Oswald:wght@700&family=Montserrat:wght@500;600;700&display=swap" rel="stylesheet">
<style>
  :root {
    --page-bg: #cfcfcf;
    --white: #ffffff;
    --navy: #12204a;
    --ink: #161c2e;
    --brand-blue: #2b5aa6;
    --photo-dark: #1b3369;
    --photo-mid: #3c5f9e;
    --photo-light: #8fa7cf;
    --rule-gray: #4a4b4f;
    --corner-gray: #545559;
  }
  * { margin: 0; padding: 0; box-sizing: border-box; }
  html, body { width: 1200px; height: 2204px; overflow: hidden; }
  body {
    background: radial-gradient(ellipse at center, #e6e6e6 0%, var(--page-bg) 70%);
    position: relative;
  }
  .billboard {
    position: absolute;
    left: 50px;
    top: 468px;
    width: 940px;
    height: 1083px;
    transform: scale(1.1702);
    transform-origin: top left;
    background: var(--white);
    overflow: hidden;
    box-shadow: 0 30px 40px rgba(0,0,0,0.22);
  }
  .billboard-shapes { position: absolute; inset: 0; width: 940px; height: 1083px; }
  .brand-name {
    position: absolute;
    left: 60px;
    top: 82px;
    width: 280px;
    font-family: "Montserrat", sans-serif;
    font-weight: 600;
    font-size: 50px;
    letter-spacing: 2px;
    color: var(--rule-gray);
  }
  .slogan {
    position: absolute;
    left: 76px;
    top: 290px;
    font-family: "Oswald", sans-serif;
    font-weight: 700;
    font-size: 104px;
    line-height: 116px;
    letter-spacing: -1px;
    color: var(--white);
    text-transform: uppercase;
    text-shadow: 3px 3px 4px rgba(0,0,0,0.35);
  }
  .services {
    position: absolute;
    left: 76px;
    top: 555px;
    width: 720px;
    display: grid;
    grid-template-columns: 355px 355px;
    row-gap: 20px;
    list-style: none;
  }
  .services li {
    font-family: "Montserrat", sans-serif;
    font-weight: 600;
    font-size: 27px;
    line-height: 32px;
    color: var(--white);
    display: flex;
    align-items: center;
    gap: 14px;
  }
  .services svg { width: 22px; height: 26px; flex: none; }
  .contact {
    position: absolute;
    left: 83px;
    top: 830px;
  }
  .contact-row { display: flex; align-items: center; gap: 28px; }
  .contact-row + .contact-row { margin-top: 22px; }
  .contact-icon {
    width: 68px; height: 68px;
    border-radius: 14px;
    background: var(--brand-blue);
    display: flex; align-items: center; justify-content: center;
    flex: none;
  }
  .contact-icon svg { width: 42px; height: 42px; }
  .phone {
    font-family: "Montserrat", sans-serif;
    font-weight: 700;
    font-size: 86px;
    color: var(--ink);
    letter-spacing: -1px;
    line-height: 1;
  }
  .website {
    font-family: "Montserrat", sans-serif;
    font-weight: 700;
    font-size: 56px;
    color: var(--ink);
    line-height: 1;
  }
  .website .domain { color: var(--brand-blue); }
</style>
</head>
<body>
  <main class="billboard">
    <svg class="billboard-shapes" viewBox="0 0 940 1083" aria-hidden="false">
      <defs>
        <linearGradient id="photoTone" x1="0" y1="1" x2="1" y2="0">
          <stop offset="0" stop-color="var(--photo-dark)"/>
          <stop offset="0.55" stop-color="var(--photo-mid)"/>
          <stop offset="1" stop-color="var(--photo-light)"/>
        </linearGradient>
      </defs>
      <polygon class="hero-photo" role="img"
        aria-label="Photo of demolition workers in hard hats and an excavator breaking ground in a cloud of dust, tinted blue"
        points="490,0 940,0 940,470 662,747 0,747 0,232 262,232"
        fill="url(#photoTone)"/>
      <polyline class="rule-top" points="0,222 265,222 490,0" fill="none" stroke="var(--rule-gray)" stroke-width="4"/>
      <polyline class="rule-bottom" points="0,757 660,757 940,478" fill="none" stroke="var(--rule-gray)" stroke-width="4"/>
      <polygon class="corner-accent" points="770,652 940,480 940,815" fill="var(--corner-gray)"/>
      <rect class="base-band" x="0" y="1048" width="940" height="35" fill="var(--navy)"/>
    </svg>

    <div class="brand-name">KESSEL</div>

    <h1 class="slogan">Watch Kessel<br>Clear the Lot</h1>

    <ul class="services">
      <li><svg viewBox="0 0 22 26"><path d="M3 2v22M3 6h8M3 13h14M3 20h8" stroke="#fff" stroke-width="2.5" fill="none"/></svg>Room Gut Out</li>
      <li><svg viewBox="0 0 22 26"><path d="M3 2v22M3 6h8M3 13h14M3 20h8" stroke="#fff" stroke-width="2.5" fill="none"/></svg>Full Demolition</li>
      <li><svg viewBox="0 0 22 26"><path d="M3 2v22M3 6h8M3 13h14M3 20h8" stroke="#fff" stroke-width="2.5" fill="none"/></svg>House Gut Out</li>
      <li><svg viewBox="0 0 22 26"><path d="M3 2v22M3 6h8M3 13h14M3 20h8" stroke="#fff" stroke-width="2.5" fill="none"/></svg>Commercial</li>
      <li><svg viewBox="0 0 22 26"><path d="M3 2v22M3 6h8M3 13h14M3 20h8" stroke="#fff" stroke-width="2.5" fill="none"/></svg>Partial Demolition</li>
      <li><svg viewBox="0 0 22 26"><path d="M3 2v22M3 6h8M3 13h14M3 20h8" stroke="#fff" stroke-width="2.5" fill="none"/></svg>Residential</li>
    </ul>

    <div class="contact">
      <div class="contact-row">
        <span class="contact-icon">
          <svg viewBox="0 0 24 24"><path d="M6.6 10.8c1.4 2.8 3.8 5.1 6.6 6.6l2.2-2.2c.3-.3.7-.4 1-.2 1.1.4 2.3.6 3.6.6.6 0 1 .4 1 1V20c0 .6-.4 1-1 1C10.6 21 3 13.4 3 4c0-.6.4-1 1-1h3.5c.6 0 1 .4 1 1 0 1.3.2 2.5.6 3.6.1.3 0 .7-.2 1z" fill="#fff"/></svg>
        </span>
        <span class="phone">(555) 018-2247</span>
      </div>
      <div class="contact-row">
        <span class="contact-icon">
          <svg viewBox="0 0 24 24" fill="none" stroke="#fff" stroke-width="1.6"><circle cx="12" cy="12" r="9"/><ellipse cx="12" cy="12" rx="4" ry="9"/><path d="M3 12h18M4.5 7.5h15M4.5 16.5h15"/></svg>
        </span>
        <span class="website">www.<span class="domain">kesseldemo</span>.com</span>
      </div>
    </div>
  </main>
</body>
</html>
```